Indonesian B2B Company (Bawo Ingredients) - Stationery Design

Bawo Ingredients needs a corporate, bold and professional-looking stationery design.

Bawo Ingredients is a new Indonesian company manufacturing, marketing and distributing various ingredients / raw materials such as flavours, fragrance, colours, sweeteners, preservatives for the food & beverage, pharmaceutical, personal care and other household goods industries.

It is a business to business (B2B) company as we supply various natural and synthetic raw materials to various consumer goods manufacturers. We therefore need a logo/identity with corporate and industrial style.

Bawo Ingredients is a startup company which belongs to a larger Tunas Mekar group of companies (http://tunasmekar.examplebiz.net/about) that focuses in the mining, petroleum and energy businesses. Bawo Ingredients would like to focus in providing good quality, safe, reliable and affordable ingredients for the industries. Our tagline is "Ingredients for Your Success"
Updates

We have updated some information including our requirements and contact details to be shown in the stationery. Please check the project brief.

Regards,

Bawo Ingredients

Target Market(s)

Manufacturers of food & beverages, personal care, pharmaceutical and other FMCG factories.

Industry/Entity Type

Business

Requirements
Must have
• Smart, professional and corporate touches in the stationery designs. We require designs for:
1. Letterhead
2. Envelope (with and without window)
3. Name card
4. Powerpoint presentation template
5. CD label
6. Small memo / with compliments card

Contact details:

Company name:
PT Bawo Ingredients

Address:
Ruko Puri Lestari Selatan, Blok F07 no: 11-12
Sunter Jaya Utara, 14350
Indonesia

Tel:+62 21 638 2097
Fax:+62 21 638 2096
Email: info@bawo-ingredients.co.id
Website: www.bawo-ingredients.co.id

```html
<!DOCTYPE html>
<html lang="en">
<head>
<meta charset="utf-8">
<title>Bawo Ingredients – Stationery</title>
<link rel="stylesheet" href="https://fonts.googleapis.com/css2?family=Barlow:wght@400;500;600&family=Pinyon+Script&display=swap">
<style>
:root{
  --red:#e01b24;
  --red-deep:#b5121b;
  --red-bright:#ee2a2f;
  --grey-text:#555;
  --paper:#ffffff;
  --paper-shade:#f1f1f1;
  --window:#d9d9d9;
  --stage:#2a2a2a;
  --pattern:linear-gradient(135deg,#c81a22 0%,#e33a2f 35%,#f08a3a 50%,#3a5ea8 62%,#c81a22 80%,#9e1119 100%);
}
*{box-sizing:border-box;margin:0;padding:0}
html,body{width:1200px;height:750px;overflow:hidden}
body{background:var(--stage);font-family:"Barlow",sans-serif;color:var(--grey-text);position:relative}
.piece{position:absolute;background:var(--paper);overflow:hidden}
.brand{color:var(--red);font-weight:500;line-height:1;white-space:nowrap}
.pattern{position:absolute;background:var(--pattern)}
.red-band{position:absolute;left:0;right:0;bottom:0;background:linear-gradient(90deg,var(--red-deep),var(--red-bright),var(--red-deep))}
.contact{font-size:5.5px;line-height:1.45;color:var(--grey-text)}
.contact .co{color:var(--red);font-weight:600}
.contact b{color:var(--red);font-weight:600;display:inline-block;width:8px}

/* Letterhead */
.letterhead{left:30px;top:30px;width:330px;height:466px}
.letterhead .masthead{position:absolute;top:42px;left:0;right:0;text-align:center}
.letterhead .brand{font-size:14px}
.letterhead .letter-body{position:absolute;left:26px;right:26px;top:112px;font-size:6.5px;line-height:1.6}
.letterhead .letter-body p{margin-bottom:8px;text-align:justify}
.letterhead .signature{position:absolute;left:40px;top:372px;width:150px;height:22px;background:var(--paper-shade);border-radius:3px}
.letterhead .footer{position:absolute;left:0;right:0;bottom:14px;text-align:center;font-size:6px;line-height:1.5}
.letterhead .footer .co{color:var(--red);font-weight:600}
.letterhead .footer b{color:var(--red);font-weight:600}
.letterhead .red-band{height:8px}

/* Folder */
.folder{left:385px;top:30px;width:330px;height:466px;background:radial-gradient(circle at 75% 20%,var(--red-bright),var(--red) 45%,var(--red-deep))}
.folder .headline{position:absolute;left:110px;top:120px;color:#fff;font-size:16px;font-weight:500;white-space:nowrap}
.folder .pattern{left:0;top:100px;width:160px;height:366px;clip-path:polygon(0 0,60% 0,100% 30%,85% 70%,100% 100%,0 100%)}

/* Business cards */
.card-front{left:740px;top:30px;width:210px;height:120px}
.card-front .logo{position:absolute;left:14px;top:50px}
.card-front .brand{font-size:10px}
.card-front .divider{position:absolute;left:104px;top:18px;width:1px;height:84px;background:#ddd}
.card-front .contact{position:absolute;left:112px;top:20px;font-size:5px}
.card-back{left:962px;top:30px;width:210px;height:120px;background:linear-gradient(135deg,var(--red-deep),var(--red-bright))}
.card-back .headline{position:absolute;right:12px;top:12px;color:#fff;font-size:6.5px;font-weight:600}
.card-back .pattern{left:0;top:26px;width:140px;height:94px;clip-path:polygon(0 0,70% 0,100% 50%,80% 100%,0 100%)}

/* Compliments slip */
.compliments{left:740px;top:170px;width:432px;height:205px}
.compliments .logo{position:absolute;left:16px;top:46px}
.compliments .brand{font-size:12px}
.compliments .script{position:absolute;right:22px;top:12px;font-family:"Pinyon Script",cursive;color:var(--red);font-size:18px;white-space:nowrap}
.compliments .contact{position:absolute;left:16px;top:102px;font-size:5.5px}
.compliments .red-band{height:10px}

/* Envelope, back with flap */
.envelope-back{left:740px;top:395px;width:432px;height:225px}
.envelope-back svg{position:absolute;left:0;top:0}
.envelope-back .headline{position:absolute;left:0;right:0;top:162px;text-align:center;font-size:10px;font-weight:500;color:#444}

/* Window envelope */
.envelope-window{left:252px;top:520px;width:440px;height:210px}
.envelope-window .logo{position:absolute;left:18px;top:32px}
.envelope-window .brand{font-size:11px}
.envelope-window .divider{position:absolute;left:112px;top:26px;width:1px;height:42px;background:#ddd}
.envelope-window .contact{position:absolute;left:120px;top:28px;font-size:4.8px}
.envelope-window .window{position:absolute;left:54px;top:92px;width:180px;height:68px;background:var(--window);border-radius:4px;border:1px solid #cfcfcf}
.envelope-window .red-band{height:12px}

/* CD label */
.cd{position:absolute;left:30px;top:520px;width:205px;height:205px}
</style>
</head>
<body>

<section class="piece letterhead" aria-label="Letterhead">
  <header class="masthead">
    <div class="brand">Bawo Ingredients</div>
  </header>
  <div class="letter-body">
    <p>December 05, 2011</p>
    <p>Mr. Hendra Wijaya</p>
    <p>Lorem ipsum dolor sit amet, consectetur adipiscing elit. Sed do eiusmod tempor incididunt ut labore et dolore magna aliqua, ut enim ad minim veniam, quis nostrud exercitation ullamco laboris.</p>
    <p>Duis aute irure dolor in reprehenderit in voluptate velit esse cillum dolore eu fugiat nulla pariatur. Excepteur sint occaecat cupidatat non proident, sunt in culpa qui officia deserunt mollit anim.</p>
    <p>Curabitur pretium tincidunt lacus, nulla gravida orci a odio, nullam varius turpis et commodo pharetra est eros bibendum elit, nec luctus magna felis sollicitudin mauris.</p>
  </div>
  <div class="signature" role="img" aria-label="Handwritten signature"></div>
  <footer class="footer">
    <div class="co">PT Bawo Ingredients</div>
    <div>Ruko Puri Lestari Selatan, Blok F07 no: 11-12, Sunter Jaya Utara, 14350, Indonesia</div>
    <div><b>T</b> +62 21 638 2097 &nbsp; <b>F</b> +62 21 638 2096 &nbsp; <b>E</b> info@bawo-ingredients.co.id &nbsp; <b>W</b> www.bawo-ingredients.co.id</div>
  </footer>
  <div class="red-band"></div>
</section>

<section class="piece folder" aria-label="Presentation folder">
  <div class="pattern" role="img" aria-label="Interlocking diamond link pattern in red, orange, blue and grey"></div>
  <h2 class="headline">Ingredients for Your Success</h2>
</section>

<section class="piece card-front" aria-label="Business card front">
  <div class="logo">
    <div class="brand">Bawo Ingredients</div>
  </div>
  <div class="divider"></div>
  <div class="contact">
    <div class="co">PT Bawo Ingredients</div>
    <div>Ruko Puri Lestari Selatan,</div>
    <div>Blok F07 no: 11-12</div>
    <div>Sunter Jaya Utara, 14350</div>
    <div>Indonesia</div>
    <br>
    <div><b>T</b>+62 21 638 2097</div>
    <div><b>F</b>+62 21 638 2096</div>
    <div><b>E</b>info@bawo-ingredients.co.id</div>
    <div><b>W</b>www.bawo-ingredients.co.id</div>
  </div>
</section>

<section class="piece card-back" aria-label="Business card back">
  <div class="pattern" role="img" aria-label="Interlocking diamond link pattern in red, orange, blue and grey"></div>
  <div class="headline">Ingredients for Your Success</div>
</section>

<section class="piece compliments" aria-label="With compliments slip">
  <div class="logo">
    <div class="brand">Bawo Ingredients</div>
  </div>
  <div class="script">with compliments</div>
  <div class="contact">
    <div class="co">PT Bawo Ingredients</div>
    <div>Ruko Puri Lestari Selatan,</div>
    <div>Blok F07 no: 11-12</div>
    <div>Sunter Jaya Utara, 14350</div>
    <div>Indonesia</div>
    <br>
    <div><b>T</b>+62 21 638 2097</div>
    <div><b>F</b>+62 21 638 2096</div>
    <div><b>E</b>info@bawo-ingredients.co.id</div>
    <div><b>W</b>www.bawo-ingredients.co.id</div>
  </div>
  <div class="red-band"></div>
</section>

<section class="piece envelope-back" aria-label="Envelope back">
  <svg width="432" height="120" viewBox="0 0 432 120">
    <defs>
      <linearGradient id="flap-fill" x1="0" y1="0" x2="1" y2="1">
        <stop offset="0" stop-color="#c81a22"/>
        <stop offset="0.4" stop-color="#e33a2f"/>
        <stop offset="0.55" stop-color="#f08a3a"/>
        <stop offset="0.7" stop-color="#3a5ea8"/>
        <stop offset="1" stop-color="#b5121b"/>
      </linearGradient>
    </defs>
    <path role="img" aria-label="Envelope flap with interlocking diamond link pattern" d="M0 0 H432 V14 L250 96 Q216 110 182 96 L0 14 Z" fill="url(#flap-fill)"/>
  </svg>
  <div class="headline">Ingredients for Your Success</div>
</section>

<section class="piece envelope-window" aria-label="Window envelope">
  <div class="logo">
    <div class="brand">Bawo Ingredients</div>
  </div>
  <div class="divider"></div>
  <div class="contact">
    <div class="co">PT Bawo Ingredients</div>
    <div>Ruko Puri Lestari Selatan,</div>
    <div>Blok F07 no: 11-12</div>
    <div>Sunter Jaya Utara, 14350</div>
    <div>Indonesia</div>
  </div>
  <div class="window"></div>
  <div class="red-band"></div>
</section>

<svg class="cd" viewBox="0 0 205 205" aria-label="CD label">
  <defs>
    <clipPath id="disc"><circle cx="102.5" cy="102.5" r="100"/></clipPath>
    <linearGradient id="cd-red" x1="0" y1="0" x2="0" y2="1">
      <stop offset="0" stop-color="#ee2a2f"/>
      <stop offset="1" stop-color="#b5121b"/>
    </linearGradient>
    <linearGradient id="cd-pattern" x1="0" y1="0" x2="1" y2="0">
      <stop offset="0" stop-color="#c81a22"/>
      <stop offset="0.35" stop-color="#f08a3a"/>
      <stop offset="0.6" stop-color="#3a5ea8"/>
      <stop offset="1" stop-color="#c81a22"/>
    </linearGradient>
  </defs>
  <circle cx="102.5" cy="102.5" r="102" fill="#e6e6e6"/>
  <g clip-path="url(#disc)">
    <rect width="205" height="205" fill="#fff"/>
    <rect width="205" height="140" fill="url(#cd-red)"/>
    <rect role="img" aria-label="Interlocking diamond link pattern" x="0" y="92" width="205" height="48" fill="url(#cd-pattern)" opacity="0.85"/>
    <rect role="img" aria-label="Interlocking diamond link pattern" x="40" y="188" width="125" height="14" fill="url(#cd-pattern)" opacity="0.85"/>
    <line x1="40" y1="155" x2="165" y2="155" stroke="#999" stroke-width="0.6"/>
    <line x1="48" y1="168" x2="157" y2="168" stroke="#999" stroke-width="0.6"/>
    <line x1="60" y1="180" x2="145" y2="180" stroke="#999" stroke-width="0.6"/>
  </g>
  <text x="102.5" y="60" text-anchor="middle" fill="#fff" font-family="Barlow, sans-serif" font-weight="500" font-size="8">Bawo Ingredients</text>
  <circle cx="102.5" cy="102.5" r="22" fill="#f0f0f0" stroke="#ccc"/>
  <circle cx="102.5" cy="102.5" r="10" fill="var(--stage)"/>
</svg>

</body>
</html>
```